Tree Pruning Website

We need a website for a tree Arborist, pruning company called Maple Crest Canopy Works. We look after all types of trees, knock down trees and prune trees. Our target market is from domestic clients to government clients and everything in between.

We would like to see the use of our main colours which are orange and green

We are not looking forward in seeing a template that we have seen before but a unique template. We have designed 5 templates ourselves and we wish for the design community to take our designs to the next level.

We have also designed a template for things that **we are not** looking for (Version 4)

To make it fair for everyone, we are also not giving out any participation payments as we have had. One winner will take all of the payment!!!

I Have attached a image of the designs and a image of a tree.

We are just looking at the PSD file been developed. We have our own team who can slice the image up into a HTML format.

Target Market(s)

Everyone who needs to cut down a tree

Industry/Entity Type

Government

Requirements
Must have
• Logo on front page
A List of our services
jQuery slider on page
Phone Number on every page

```html
<!DOCTYPE html>
<html lang="en">
<head>
<meta charset="utf-8">
<title>Maple Crest Canopy Works</title>
<link href="https://fonts.googleapis.com/css2?family=Open+Sans:wght@400;600;700&family=Oswald:wght@400;500&display=swap" rel="stylesheet">
<style>
:root{
  --green:#6fae2f;
  --green-dark:#3f7d1c;
  --green-light:#9ccf5a;
  --orange:#f08a1c;
  --ink:#4a4a4a;
  --muted:#8a8a8a;
  --panel:#f1f1ec;
  --footer:#2e2e2c;
  --footer-deep:#1e1e1c;
  --white:#ffffff;
}
*{box-sizing:border-box;margin:0;padding:0}
html,body{width:1200px;height:2240px;overflow:hidden}
body{font-family:"Open Sans",Arial,sans-serif;color:var(--ink);background:var(--white);position:relative}
.abs{position:absolute}
.heading{font-family:"Oswald","Arial Narrow",sans-serif;font-weight:500;text-transform:uppercase;letter-spacing:.5px}

/* header */
.brand{left:40px;top:24px;display:flex;align-items:center;gap:14px}
.brand-dot{width:64px;height:64px;border-radius:50%;background:var(--green)}
.brand-name{font-family:"Oswald",sans-serif;font-weight:500;font-size:30px;color:var(--green-dark);line-height:1.05;width:240px}
.follow{left:460px;top:36px;display:flex;align-items:center;gap:16px;font-size:22px;font-weight:600;color:var(--ink)}
.follow span.soc{width:38px;height:38px;border-radius:50%;background:var(--green)}
.phones{right:40px;top:26px;font-size:17px;line-height:38px;color:var(--ink)}
.phones div{display:flex;align-items:center;gap:10px}
.nav{left:400px;top:150px;display:flex;gap:40px;font-size:14px;font-weight:600;color:var(--green-dark)}
.nav .active{background:var(--green);color:var(--white);padding:6px 12px;margin-top:-6px}
.drop{left:628px;top:202px;width:112px}
.drop div,.drop2 div{background:var(--green-dark);color:var(--white);font-size:11px;padding:7px 10px;margin-bottom:4px;border-bottom:2px solid var(--green)}
.drop2{left:744px;top:250px;width:112px}

/* hero */
.hero{left:0;top:190px;width:1200px;height:620px}
.hero-tree{left:340px;top:20px;width:520px;height:560px;border-radius:48% 48% 8px 8px;background:radial-gradient(ellipse at 50% 35%,#5c9a2e,#2f6a18 70%)}
.hero-worker{left:870px;top:140px;width:210px;height:460px;border-radius:40px 40px 0 0;background:linear-gradient(#f4a03a,#e07d1a 45%,#3d3d3d)}
.hero-card{left:0;top:240px;width:390px;height:220px;background:rgba(40,40,40,.88);padding:22px 26px;color:#ddd}
.hero-card h1{font-family:"Oswald",sans-serif;font-weight:400;font-size:26px;color:var(--green-light);margin-bottom:10px}
.hero-card p{font-size:12px;line-height:17px}
.btn{display:inline-block;background:#777;color:var(--white);font-size:11px;font-weight:700;padding:6px 14px;border-radius:12px;margin-top:12px;text-transform:uppercase}
.btn.dark{background:#3a3a3a}
.dots{left:40px;top:782px;display:flex;gap:10px}
.dots span{width:12px;height:12px;border-radius:50%;background:#bbb}
.dots span:first-child{background:var(--green)}

/* uses */
.uses{left:0;top:860px;width:1200px;height:480px;background:linear-gradient(#e8e8e2,#fafaf7);display:flex;gap:36px;padding:22px 38px}
.use{width:264px}
.use h2{font-size:22px;color:var(--green-dark);margin-bottom:10px}
.use .photo{height:150px}
.use p{font-size:12px;line-height:18px;color:var(--ink);margin-top:12px}

/* main */
.side{left:0;top:1380px;width:260px}
.side h3{background:var(--green);color:var(--white);font-size:22px;padding:10px 30px;border-radius:0 22px 0 0}
.side ul{list-style:none;background:var(--panel);padding:8px 0}
.side li{font-size:13px;padding:9px 0 9px 40px;margin:5px 16px 5px 12px;background:linear-gradient(#e6f2d8,#cfe6b4);border-left:6px solid var(--green);color:var(--ink)}
.side li.on{background:var(--orange);border-left-color:#c96a08;color:var(--white)}
.about{left:306px;top:1380px;width:860px}
.about h2,.gallery h2{font-size:24px;color:var(--green-dark);margin-bottom:10px}
.about .photo{width:190px;height:170px;float:left;margin-right:26px}
.about p{font-size:12px;line-height:19px}
.gallery{left:306px;top:1640px;width:860px}
.thumbs{display:flex;gap:14px}
.thumbs div{width:84px;height:64px;border:3px solid var(--white);box-shadow:0 1px 4px rgba(0,0,0,.3);background:linear-gradient(#f2a23c,#3f7d1c)}

/* footer */
.footer{left:0;top:1830px;width:1200px;height:370px;background:var(--footer);color:#cfcfcf;display:flex;padding:30px 40px;gap:40px}
.footer h4{font-size:22px;color:var(--white);margin-bottom:14px}
.footer ul{list-style:none;font-size:12px;line-height:19px}
.footer .col{width:240px}
.footer p{font-size:12px;line-height:19px}
.footer .sig{color:var(--orange);text-align:right;margin-top:12px}
.footer .addr{color:var(--orange)}
.bottom{left:0;top:2200px;width:1200px;height:40px;background:var(--footer-deep);color:#bbb;font-size:11px;text-align:center;line-height:40px}
</style>
</head>
<body>

<header>
  <div class="abs brand"><span class="brand-dot"></span><span class="brand-name">Maple Crest Canopy Works</span></div>
  <div class="abs follow">Follow us : <span class="soc"></span><span class="soc"></span><span class="soc"></span></div>
  <div class="abs phones">
    <div><svg width="22" height="22" viewBox="0 0 24 24"><rect x="2" y="2" width="20" height="20" fill="#3a3a3a"/><path d="M7 5h3l1 4-2 1a9 9 0 0 0 5 5l1-2 4 1v3a2 2 0 0 1-2 2A14 14 0 0 1 5 7a2 2 0 0 1 2-2z" fill="#fff"/></svg>0400 218 735</div>
    <div><svg width="22" height="22" viewBox="0 0 24 24"><rect x="2" y="2" width="20" height="20" fill="#3a3a3a"/><path d="M7 5h3l1 4-2 1a9 9 0 0 0 5 5l1-2 4 1v3a2 2 0 0 1-2 2A14 14 0 0 1 5 7a2 2 0 0 1 2-2z" fill="#fff"/></svg>0400 218 735</div>
  </div>
  <nav class="abs nav"><span>HOME</span><span>ABOUT US</span><span class="active">OUR SERVICES</span><span>GET A QUOTE</span><span>OUR WORK</span><span>CONTACT US</span></nav>
</header>

<section class="abs hero">
  <div class="abs hero-tree" role="img" aria-label="Large leafy green tree"></div>
  <div class="abs hero-worker" role="img" aria-label="Arborist in orange safety gear holding a chainsaw"></div>
  <div class="abs hero-card">
    <h1>Maple Crest Canopy Works</h1>
    <p>We care for every kind of tree, from careful crown pruning to complete removal. Our certified arborists work safely on homes, businesses and public land, leaving each site clean and each tree healthier than before. Ask about seasonal care plans and free on-site quotes today.</p>
    <span class="btn dark">Read more</span>
  </div>
</section>
<div class="abs drop"><div>SERVICES 1</div><div>SERVICES 2</div><div>SERVICES 3</div><div>SERVICES 4</div><div>SERVICES 5</div></div>
<div class="abs drop2"><div>SERVICES 2</div><div>SERVICES 3</div><div>SERVICES 4</div></div>
<div class="abs dots"><span></span><span></span><span></span><span></span></div>

<section class="abs uses">
  <article class="use"><h2 class="heading">Domestic use</h2><div class="photo" role="img" aria-label="Crew pruning a garden tree beside a house" style="background:linear-gradient(#8cc06a,#4e7f2c)"></div>
    <p>Overgrown gardens, leaning trunks and blocked gutters are handled with care. We prune, shape and remove trees around your home while protecting lawns, fences and roofs, then clear every branch away before we leave.</p><span class="btn">Read more</span></article>
  <article class="use"><h2 class="heading">Commercial use</h2><div class="photo" role="img" aria-label="Street trees outside commercial buildings" style="background:linear-gradient(#b9a88c,#5e7a3c)"></div>
    <p>Shopping centres, offices and car parks need tidy, safe trees. Our teams work to your schedule, keep walkways open, and supply clear reports so managers can plan ongoing maintenance with no disruption to business.</p><span class="btn">Read more</span></article>
  <article class="use"><h2 class="heading">Government use</h2><div class="photo" role="img" aria-label="Arborists working on trees in a public park" style="background:linear-gradient(#9ec7e0,#4d7d2a)"></div>
    <p>Councils and agencies trust us with parks, roadsides and school grounds. We meet strict safety standards, carry full insurance and deliver detailed risk assessments for large public tree programs across the region.</p><span class="btn">Read more</span></article>
  <article class="use"><h2 class="heading">Non-profit use</h2><div class="photo" role="img" aria-label="Volunteers planting young trees" style="background:linear-gradient(#a7d07a,#3f7d1c)"></div>
    <p>Community groups, clubs and charities receive reduced rates for tree health checks, planting days and storm clean up. We are proud to support the local projects that keep our neighbourhoods green and welcoming.</p><span class="btn">Read more</span></article>
</section>

<aside class="abs side">
  <h3 class="heading">Our services</h3>
  <ul><li>Diagnosis</li><li>Treatment</li><li>Pruning</li><li class="on">Tree Removal</li><li>Stump removal</li><li>Cabling &amp; Bracing</li><li>Arborist Consults</li><li>Tree Protection</li></ul>
</aside>

<section class="abs about">
  <h2 class="heading">About us</h2>
  <div class="photo" role="img" aria-label="Team of arborists standing in a row" style="background:linear-gradient(#9ccf5a,#3f7d1c)"></div>
  <p>We began as a small family crew with one truck and a love of big old trees. Today our qualified arborists look after private yards, commercial grounds and public parks across the region. Every job starts with a careful inspection, a clear written quote and an honest plan. We use modern climbing gear and low impact machinery, recycle green waste into mulch, and always leave your site safe, swept and tidy. Our aim is simple: healthy trees, happy clients and zero accidents.</p>
</section>

<section class="abs gallery">
  <h2 class="heading">Image gallery</h2>
  <div class="thumbs" role="img" aria-label="Gallery of tree work photos">
    <div></div><div></div><div></div><div></div><div></div><div></div><div></div><div></div>
  </div>
</section>

<footer class="abs footer">
  <div class="col"><h4 class="heading">Quick links</h4><ul><li>Home</li><li>About us</li><li>Services</li><li>Our work</li><li>Privacy policy</li><li>Use of Terms</li></ul></div>
  <div class="col"><h4 class="heading">Services</h4><ul><li>Diagnosis</li><li>Treatment</li><li>Pruning</li><li>Tree Removal</li><li>Stump Removal</li><li>Cabling &amp; Bracing</li><li>Arborist Consults</li><li>Tree Protection</li></ul></div>
  <div class="col" style="width:300px"><h4 class="heading">Testimonials</h4><p>"The crew arrived on time, explained every step and removed two huge gums without touching our shed. They cleaned up so well you would never know they had been here. Fair price, friendly people and great advice for the trees we kept."</p><p class="sig">- Mr. Hollins</p></div>
  <div class="col"><h4 class="heading">Contact us</h4><p class="addr">41 Birchwood Lane,<br>Fernvale, WA 6112<br>Phone: 0400 218 735<br>Phone: 0400 218 735</p></div>
</footer>
<div class="abs bottom">Copyright 2013 All right reserved</div>

</body>
</html>
```